Personal Motivational Quote Poster Design

I would like to create a poster with some of my favorite quotes to hang in my office. I did similar projects in 2012 and 2014. I've uploaded the winning designs so you can get a better idea of what I'm looking for. I will provide feedback on your design within 24 hours of receiving it.

The poster must contain the following quotes:

“What the pupil must learn, if he learns anything at all, is that the world will do most of the work for you, provided you cooperate with it by identifying how it really works and aligning with those realities. If we do not let the world teach us, it teaches us a lesson.” - Harold Quenby

“I tackle every big new problem by asking two questions: Who has dealt with this problem well? And what can we learn from them?” - Walt Prisco

“If we can really understand the problem, the answer will come out of it, because the answer is not separate from the problem.” - Ravindra Selvapathi

“Success is nothing more than a few simple disciplines, practiced every day; while failure is simply a few errors in judgment, repeated every day. It is the accumulative weight of our disciplines and our judgments that leads us to either fortune or failure.” - Ned Falco

“Inaction breeds doubt and fear. Action breeds confidence and courage.” - Rufus Pembrook

“What’s the one thing you can do, such that by doing it, everything else will be easier or unnecessary?” - Lyle Dorsey

Requirements
Must have
• The poster will be 24" high x 36" long and printed on canvas, so the image you create needs to have a resolution of at least 2700 x 3900.
Nice to have
• I don't have an exact vision for how the poster should look, so I am totally open to you using your creativity to develop, arrange and present the content as you'd like.

That said, I would like an image (photo or posterized image) of the person being quoted along with each quote. I do not have specific images that I would like you to use, so you will need to find the images on your own.

The images don't need to be perfect... I am more interested in the poster relating the essence of the quotes and the people being quoted than I am in perfect photographic images of the people being quoted.

```html
<!DOCTYPE html>
<html lang="en">
<head>
<meta charset="utf-8">
<title>Favourite Quotes Poster</title>
<link rel="stylesheet" href="https://fonts.googleapis.com/css2?family=Delius&family=Kalam:wght@300&display=swap">
<style>
  :root {
    --bg: #111111;
    --rust: #8a5336;
    --sage: #6b7a57;
    --umber: #5d4733;
    --bronze: #6b5339;
    --slate: #626262;
    --ink: #f3f0ea;
    --frame: #ecebe8;
  }
  html, body {
    margin: 0;
    padding: 0;
    width: 1200px;
    height: 800px;
    overflow: hidden;
    background: var(--bg);
  }
  .poster {
    display: block;
    width: 1200px;
    height: 800px;
  }
  .quote {
    font-family: "Delius", "Comic Sans MS", sans-serif;
    fill: var(--ink);
  }
  .author {
    font-family: "Kalam", "Delius", cursive;
    font-weight: 300;
    fill: var(--ink);
    font-size: 19px;
  }
  .frame {
    fill: none;
    stroke: var(--frame);
    stroke-width: 2.2;
  }
  .panel-rust { fill: var(--rust); }
  .panel-sage { fill: var(--sage); }
  .panel-umber { fill: var(--umber); }
  .panel-bronze { fill: var(--bronze); }
  .panel-slate { fill: var(--slate); }
  .s-sm { font-size: 18px; }
  .s-md { font-size: 21px; }
  .s-lg { font-size: 27px; }
  .s-xl { font-size: 33px; }
</style>
</head>
<body>
<svg class="poster" viewBox="0 0 1200 800" xmlns="http://www.w3.org/2000/svg">
  <defs>
    <radialGradient id="portrait-warm" cx="50%" cy="45%" r="60%">
      <stop offset="0" stop-color="#b07a5e" stop-opacity="0.85"/>
      <stop offset="1" stop-color="#8a5336" stop-opacity="0"/>
    </radialGradient>
    <radialGradient id="portrait-sage" cx="50%" cy="45%" r="60%">
      <stop offset="0" stop-color="#93a07f" stop-opacity="0.8"/>
      <stop offset="1" stop-color="#6b7a57" stop-opacity="0"/>
    </radialGradient>
    <radialGradient id="portrait-grey" cx="50%" cy="45%" r="60%">
      <stop offset="0" stop-color="#555555" stop-opacity="0.9"/>
      <stop offset="1" stop-color="#111111" stop-opacity="0"/>
    </radialGradient>
    <radialGradient id="portrait-umber" cx="50%" cy="45%" r="60%">
      <stop offset="0" stop-color="#7e6a55" stop-opacity="0.85"/>
      <stop offset="1" stop-color="#5d4733" stop-opacity="0"/>
    </radialGradient>
    <radialGradient id="portrait-sand" cx="50%" cy="45%" r="60%">
      <stop offset="0" stop-color="#c2b29c" stop-opacity="0.85"/>
      <stop offset="1" stop-color="#6b5339" stop-opacity="0"/>
    </radialGradient>
    <radialGradient id="portrait-slate" cx="50%" cy="45%" r="60%">
      <stop offset="0" stop-color="#3c3c3c" stop-opacity="0.85"/>
      <stop offset="1" stop-color="#626262" stop-opacity="0"/>
    </radialGradient>
  </defs>

  <!-- Quenby card -->
  <g class="card card-quenby">
    <rect class="panel-rust" x="19" y="38" width="598" height="258"/>
    <rect role="img" aria-label="Posterized portrait of Harold Quenby" x="440" y="150" width="150" height="146" fill="url(#portrait-warm)"/>
    <polygon class="frame" points="45,24 635,71 615,325 24,279"/>
    <text class="quote s-lg" x="54" y="58">"</text>
    <text class="quote s-md">
      <tspan x="80" y="86">What the pupil must learn, if he learns anything at</tspan>
      <tspan x="50" y="113">all, is that the world will do most of the work for you,</tspan>
      <tspan x="50" y="140">provided you cooperate with it by identifying how it</tspan>
      <tspan x="50" y="167">really works and aligning with those realities.</tspan>
    </text>
    <text class="quote s-lg">
      <tspan x="62" y="204" textLength="512" lengthAdjust="spacing">If we do not let the world teach us, it</tspan>
      <tspan x="50" y="240">teaches us a lesson."</tspan>
    </text>
    <text class="author" x="56" y="266">- Harold Quenby</text>
  </g>

  <!-- Pembrook card -->
  <g class="card card-pembrook">
    <polygon class="panel-sage" points="609,51 1169,25 1178,237 620,252"/>
    <rect role="img" aria-label="Posterized portrait of Rufus Pembrook" x="635" y="95" width="140" height="142" fill="url(#portrait-sage)"/>
    <rect class="frame" x="606" y="36" width="545" height="204"/>
    <text class="quote" text-anchor="end">
      <tspan x="1130" y="107"><tspan class="s-xl">Inaction</tspan> <tspan class="s-md">breeds</tspan> <tspan class="s-lg">doubt and fear.</tspan></tspan>
      <tspan x="1130" y="147"><tspan class="s-xl">Action</tspan> <tspan class="s-md">breeds</tspan> <tspan class="s-lg">confidence and courage."</tspan></tspan>
    </text>
    <text class="author" x="1130" y="222" text-anchor="end">- Rufus Pembrook</text>
  </g>

  <!-- Falco card -->
  <g class="card card-falco">
    <polygon class="panel-umber" points="596,255 1170,268 1172,523 594,510"/>
    <rect role="img" aria-label="Posterized portrait of Ned Falco speaking" x="1010" y="400" width="155" height="120" fill="url(#portrait-umber)"/>
    <polygon class="frame" points="592,239 1173,275 1168,538 584,502"/>
    <text class="quote s-md">
      <tspan x="626" y="295" textLength="500" lengthAdjust="spacing">"<tspan class="s-xl">Success</tspan> is nothing more than a few simple</tspan>
      <tspan x="626" y="337" textLength="500" lengthAdjust="spacing">disciplines, practiced every day; while <tspan class="s-xl">failure</tspan> is</tspan>
      <tspan x="626" y="362" textLength="500" lengthAdjust="spacing">simply a few errors in judgment, repeated every day.</tspan>
      <tspan x="626" y="395" textLength="500" lengthAdjust="spacing">It is the accumulative weight of <tspan class="s-lg">our disciplines</tspan></tspan>
      <tspan x="626" y="428" textLength="500" lengthAdjust="spacing"><tspan class="s-lg">and our judgments</tspan> that <tspan class="s-lg">leads us to either</tspan></tspan>
    </text>
    <text class="quote s-lg" x="1126" y="462" text-anchor="end">fortune or failure."</text>
    <text class="author" x="1126" y="516" text-anchor="end">- Ned Falco</text>
  </g>

  <!-- Prisco card -->
  <g class="card card-prisco">
    <rect role="img" aria-label="Monochrome portrait of Walt Prisco" x="140" y="360" width="150" height="132" fill="url(#portrait-grey)"/>
    <rect class="frame" x="34" y="305" width="574" height="187"/>
    <text class="quote s-md">
      <tspan x="60" y="344">"I tackle every big new problem by asking two</tspan>
      <tspan x="60" y="384">questions: <tspan class="s-xl">Who</tspan> has dealt with this problem well?</tspan>
      <tspan x="60" y="424">And <tspan class="s-xl">what</tspan> can we learn from them?"</tspan>
    </text>
    <text class="author" x="66" y="476">- Walt Prisco</text>
  </g>

  <!-- Selvapathi card -->
  <g class="card card-selvapathi">
    <polygon class="panel-bronze" points="23,533 598,520 603,727 28,740"/>
    <rect role="img" aria-label="Posterized portrait of Ravindra Selvapathi" x="355" y="585" width="135" height="145" fill="url(#portrait-sand)"/>
    <polygon class="frame" points="19,539 604,489 622,686 37,739"/>
    <text class="quote s-md">
      <tspan x="55" y="557">"If we can really understand the problem, the answer</tspan>
      <tspan x="55" y="597">will come out of it, because <tspan class="s-xl">the answer is not</tspan></tspan>
      <tspan x="55" y="637"><tspan class="s-xl">separate from the problem."</tspan></tspan>
    </text>
    <text class="author" x="60" y="690">- Ravindra Selvapathi</text>
  </g>

  <!-- Dorsey card -->
  <g class="card card-dorsey">
    <polygon class="panel-slate" points="609,535 1169,525 1178,747 598,757"/>
    <rect role="img" aria-label="Posterized portrait of Lyle Dorsey smiling" x="640" y="620" width="140" height="130" fill="url(#portrait-slate)"/>
    <polygon class="frame" points="603,535 1168,525 1174,737 610,747"/>
    <text class="quote s-md" text-anchor="end">
      <tspan x="1145" y="595" textLength="500" lengthAdjust="spacing">"What's <tspan class="s-xl">the one thing you can do,</tspan></tspan>
      <tspan x="1145" y="624">such that by doing it, everything else will be easier</tspan>
      <tspan x="1145" y="652">or unnecessary?"</tspan>
    </text>
    <text class="author" x="1145" y="702" text-anchor="end">- Lyle Dorsey</text>
  </g>
</svg>
</body>
</html>
```